Law Firm Business Card

This is a business card for a law firm that serves US military and veterans.

The card must have ONLY the following (we want an uncluttered look):

- Company logo (PNG, GIF, JPEG copies uploaded)
- A tagline reading: "a law firm for service members and veterans"
- My name and title: "Tobias Marlow" and "Attorney"
- My email: "tobias.marlow@brinmoorlegal.com"
- My number: "855-FIRM-ONE (347-6663)"

We are looking for a clean, simple layout with only the above information, likely printed on a bright white cotton stock. The font of our logo is DIN 1451, and the font used on our website is Helvetica Neue. The color of our logo is #336699, and we probably want the tagline in that color also, and my contact information in a dark grey. Please review our website at www.brinmoorlegal.com to ensure your card design complements our website style.

Thanks and we look forward to seeing your submissions.

A few notes:

- Two-sided submissions are ok
- Please don't add graphics (scales of justice, judges hammer, etc)

```html
<!DOCTYPE html>
<html lang="en">
<head>
<meta charset="utf-8">
<title>Brinmoor Legal – Business Card</title>
<link rel="stylesheet" href="https://fonts.googleapis.com/css2?family=Barlow+Condensed:wght@500;600&family=Barlow:wght@500;600&family=Tinos&display=swap">
<style>
  :root {
    --brand-blue: #2767c9;
    --ink: #1d1d1d;
    --rule: #cfd3da;
    --paper: #ffffff;
    --backdrop: #e9e7e3;
  }
  * { box-sizing: border-box; margin: 0; padding: 0; }
  html, body { width: 1200px; height: 1049px; overflow: hidden; }
  body { background: var(--backdrop); position: relative; font-family: "Barlow", sans-serif; }

  .card {
    position: absolute;
    width: 620px;
    height: 354px;
    overflow: hidden;
    box-shadow: 0 6px 18px rgba(0,0,0,.18);
  }

  /* Front */
  .card--front { left: 60px; top: 110px; background: var(--paper); }
  .wordmark {
    position: absolute;
    left: 38px;
    top: 60px;
    font-family: "Barlow Condensed", sans-serif;
    font-weight: 600;
    color: var(--brand-blue);
    font-size: 54px;
    line-height: .95;
    letter-spacing: .5px;
    text-transform: uppercase;
  }
  .details {
    position: absolute;
    left: 318px;
    right: 20px;
    top: 118px;
    bottom: 34px;
    padding-left: 18px;
    border-left: 1.5px solid var(--rule);
  }
  .name-line { font-weight: 600; font-size: 23px; color: var(--brand-blue); white-space: nowrap; }
  .name-line .title { font-size: 15px; color: var(--ink); font-weight: 600; }
  .tagline {
    font-family: "Tinos", serif;
    color: var(--brand-blue);
    font-size: 19px;
    line-height: 1.15;
    margin-top: 4px;
    width: 260px;
  }
  .contacts { list-style: none; margin-top: 22px; }
  .contacts li {
    display: flex;
    align-items: center;
    gap: 8px;
    font-size: 15px;
    font-weight: 500;
    color: var(--ink);
    margin-bottom: 6px;
    white-space: nowrap;
  }
  .contacts svg { width: 15px; height: 15px; flex: none; }
  .tab {
    position: absolute;
    bottom: 0;
    height: 10px;
    background: var(--brand-blue);
    border-radius: 6px 6px 0 0;
  }
  .tab--left { left: 150px; width: 160px; }
  .tab--right { left: 385px; width: 210px; }

  /* Back */
  .card--back {
    left: 520px; top: 560px;
    background: var(--brand-blue);
    display: flex;
    align-items: center;
    justify-content: center;
  }
  .card--back .wordmark {
    position: static;
    color: var(--paper);
    font-size: 84px;
    text-align: center;
  }
</style>
</head>
<body>
  <section class="card card--front" aria-label="Business card front">
    <div class="wordmark">Brinmoor<br>Legal</div>

    <div class="details">
      <p class="name-line">Tobias Marlow<span class="title">, Attorney</span></p>
      <p class="tagline">A Law Firm For Service Members And Veterans</p>
      <ul class="contacts">
        <li>
          <svg viewBox="0 0 16 16" aria-hidden="true"><circle cx="8" cy="8" r="7" fill="none" stroke="var(--brand-blue)" stroke-width="1.4"/><path d="M6 4.5c-1 1-1 3.5 1 5.5s4.5 2 5.5 1l-1.3-1.3-1.2.8c-1-.4-2.3-1.7-2.7-2.7l.8-1.2z" fill="var(--brand-blue)"/></svg>
          855-FIRM-ONE (347-6663)
        </li>
        <li>
          <svg viewBox="0 0 16 16" aria-hidden="true"><rect x="1" y="3.5" width="14" height="9.5" rx="1.2" fill="var(--brand-blue)"/><path d="M1.5 4.5 8 9l6.5-4.5" fill="none" stroke="#fff" stroke-width="1.3"/></svg>
          tobias.marlow@brinmoorlegal.com
        </li>
        <li>
          <svg viewBox="0 0 16 16" aria-hidden="true"><g fill="none" stroke="var(--brand-blue)" stroke-width="1.2"><circle cx="8" cy="8" r="6.5"/><ellipse cx="8" cy="8" rx="3" ry="6.5"/><path d="M1.5 8h13M2.7 4.5h10.6M2.7 11.5h10.6"/></g></svg>
          www.brinmoorlegal.com
        </li>
      </ul>
    </div>

    <span class="tab tab--left"></span>
    <span class="tab tab--right"></span>
  </section>

  <section class="card card--back" aria-label="Business card back">
    <div class="wordmark">Brinmoor<br>Legal</div>
  </section>
</body>
</html>
```